New Business card design to reflect rebrand

I would like a business card design with a good base colour for our new logo and also a placeholder for a profile pic of the card holder. the design needs to be editable to the point that we can easily change the picture of the person and use that design for printmerlo etc. we are looking at a metalic finish business card so will need a good base colour to bring out the finish.

Target Market(s)

prospective customers

Industry/Entity Type

Business

Contact Information for Business Card

I would like one editable design that we can change the name of the card holder and profile picture. The design need to be in a format that be send to printmerlo etc.

Our address is Fenwick Lodge, Copse Lane, Ashcombe Vale, GU14 3TP Tel no. 01483 556172

Requirements
Must have
• place holder for a profile pic for the card holder. in AI or preferably PSD format

```html
<!DOCTYPE html>
<html lang="en">
<head>
<meta charset="utf-8">
<title>Corvane Workplace Services – Business Card</title>
<link rel="stylesheet" href="https://fonts.googleapis.com/css2?family=Jost:wght@400;500;600;700&display=swap">
<style>
  :root {
    --page-bg: #2b2c2b;
    --card-white: #f7f7f6;
    --navy: #34475f;
    --navy-deep: #1f2d40;
    --navy-glow: #3d5570;
    --orange: #e0601f;
    --ink: #1c1c1c;
    --photo-grey: #c9c9c9;
    --photo-frame: #d9d9d9;
  }
  * { box-sizing: border-box; margin: 0; padding: 0; }
  html, body {
    width: 1200px; height: 1200px; overflow: hidden;
    background: var(--page-bg);
    font-family: "Jost", sans-serif;
  }
  .card {
    position: absolute;
    top: 442px;
    width: 512px;
    height: 298px;
    overflow: hidden;
  }
  .card--front { left: 81px; background: var(--card-white); }
  .card--back {
    left: 607px;
    background: radial-gradient(ellipse at 50% 45%, var(--navy-glow) 0%, var(--navy) 35%, var(--navy-deep) 100%);
  }

  .brand { position: absolute; }
  .brand__name {
    display: block;
    font-weight: 500;
    line-height: 1;
    letter-spacing: 0.02em;
  }
  .brand__sub {
    display: block;
    font-weight: 500;
    letter-spacing: 0.2em;
    line-height: 1;
  }
  .card--front .brand { left: 25px; top: 46px; color: var(--navy); }
  .card--front .brand__name { font-size: 42px; }
  .card--front .brand__sub { font-size: 14px; margin-top: 6px; }

  .card--back .brand { left: 0; right: 0; top: 118px; text-align: center; color: #ffffff; }
  .card--back .brand__name { font-size: 44px; }
  .card--back .brand__sub { font-size: 14px; margin-top: 8px; }

  .profile-photo {
    position: absolute;
    left: 382px; top: 24px;
    width: 106px; height: 106px;
    border-radius: 3px;
    background: linear-gradient(180deg, var(--photo-frame), var(--photo-grey));
  }
  .holder {
    position: absolute;
    left: 362px; top: 136px; width: 146px;
    text-align: center;
  }
  .holder__name { font-size: 17px; font-weight: 700; color: var(--orange); letter-spacing: 0.03em; line-height: 1; }
  .holder__title { font-size: 9.5px; font-weight: 600; color: var(--ink); margin-top: 3px; line-height: 1; }

  .address {
    position: absolute;
    left: 25px; top: 243px;
    font-size: 13.5px; color: var(--ink); line-height: 18px;
  }
  .contact {
    position: absolute;
    right: 24px; top: 224px;
    list-style: none;
    font-size: 13.5px; color: var(--ink); line-height: 18px;
  }
  .contact__item { display: flex; justify-content: flex-end; align-items: center; gap: 7px; }
  .contact__icon { width: 11px; height: 11px; flex: none; }

  .accent-band { position: absolute; left: 0; bottom: 0; width: 512px; height: 16px; }

  .web-address {
    position: absolute; left: 0; right: 0; top: 259px;
    text-align: center; color: #e4e8ee; font-size: 12.5px;
  }
</style>
</head>
<body>

<section class="card card--front" aria-label="Business card front">
  <div class="brand">
    <span class="brand__name">CORVANE</span>
    <span class="brand__sub">WORKPLACE SERVICES</span>
  </div>

  <div class="profile-photo" role="img" aria-label="Profile photo of the card holder"></div>
  <div class="holder">
    <p class="holder__name">YOUR NAME</p>
    <p class="holder__title">JOB TITLE</p>
  </div>

  <p class="address">Fenwick Lodge, Copse Lane<br>Ashcombe Vale, GU14 3TP</p>

  <ul class="contact">
    <li class="contact__item">01483 556172
      <svg class="contact__icon" viewBox="0 0 11 11" aria-hidden="true">
        <rect width="11" height="11" rx="1.5" fill="var(--orange)"/>
        <path d="M2.5 4.2 Q5.5 2 8.5 4.2 L7.6 5 L6.6 4.4 H4.4 L3.4 5 Z M3.4 5.6 H7.6 V8.4 H3.4 Z" fill="#fff"/>
      </svg>
    </li>
    <li class="contact__item">info@corvaneWS.com
      <svg class="contact__icon" viewBox="0 0 11 11" aria-hidden="true">
        <rect width="11" height="11" rx="1.5" fill="var(--orange)"/>
        <rect x="2.3" y="3.3" width="6.4" height="4.4" fill="none" stroke="#fff" stroke-width="0.9"/>
        <path d="M2.3 3.3 L5.5 5.8 L8.7 3.3" fill="none" stroke="#fff" stroke-width="0.9"/>
      </svg>
    </li>
    <li class="contact__item">www.corvaneWS.com
      <svg class="contact__icon" viewBox="0 0 11 11" aria-hidden="true">
        <rect width="11" height="11" rx="1.5" fill="var(--orange)"/>
        <circle cx="5.5" cy="5.5" r="3" fill="none" stroke="#fff" stroke-width="0.9"/>
        <path d="M2.5 5.5 H8.5 M5.5 2.5 V8.5" stroke="#fff" stroke-width="0.7"/>
      </svg>
    </li>
  </ul>

  <svg class="accent-band" viewBox="0 0 512 16" preserveAspectRatio="none" aria-hidden="true">
    <rect width="512" height="16" fill="var(--navy)"/>
    <polygon points="0,0 352,0 340,16 0,16" fill="var(--orange)"/>
    <polygon points="352,0 358,0 346,16 340,16" fill="#ffffff"/>
  </svg>
</section>

<section class="card card--back" aria-label="Business card back">
  <div class="brand">
    <span class="brand__name">CORVANE</span>
    <span class="brand__sub">WORKPLACE SERVICES</span>
  </div>
  <p class="web-address">www.corvaneWS.com</p>
</section>

</body>
</html>
```